Book Cover for Productivity Book

I need a book cover for my latest publication "On Momentum: The Gathered Insights of the Swiftest Worker Breathing"

You can see my branding at www.quillmarrow.com

This is meant to be my epic pinaccle work on productivity, I want it to look like the end all be all word on productivity.

Target Market(s)

entrepreneurs

```html
<!DOCTYPE html>
<html lang="en">
<head>
<meta charset="utf-8">
<title>On Momentum – Book Cover</title>
<link rel="stylesheet" href="https://fonts.googleapis.com/css2?family=Anton&family=Montserrat:wght@600&display=swap">
<style>
  :root {
    --backdrop: #d3d0b9;
    --cover-yellow: #cdbd0c;
    --cover-red: #6b0000;
    --title-navy: #0d1b2a;
    --subtitle-white: #e6e6e6;
  }
  html, body {
    margin: 0;
    padding: 0;
    width: 1200px;
    height: 1200px;
    overflow: hidden;
    background: var(--backdrop);
  }
  .book-cover {
    position: absolute;
    left: 260px;
    top: 100px;
    width: 680px;
    height: 1000px;
    display: flex;
  }
  .spine-panel {
    position: relative;
    width: 320px;
    height: 100%;
    background: var(--cover-yellow);
  }
  .main-title {
    position: absolute;
    right: 14px;
    bottom: 12px;
    margin: 0;
    writing-mode: vertical-rl;
    transform: rotate(180deg);
    font-family: "Anton", "Impact", sans-serif;
    font-weight: 400;
    color: var(--title-navy);
    text-transform: uppercase;
    white-space: nowrap;
  }
  .main-title .title-prefix {
    display: block;
    font-size: 86px;
    line-height: 0.86;
    letter-spacing: -1px;
  }
  .main-title .title-word {
    display: block;
    font-size: 142px;
    line-height: 0.9;
    letter-spacing: 1px;
  }
  .subtitle-panel {
    flex: 1;
    height: 100%;
    background: var(--cover-red);
    display: flex;
    align-items: center;
    justify-content: center;
  }
  .subtitle {
    margin: 0;
    padding-bottom: 60px;
    font-family: "Montserrat", "Helvetica Neue", Arial, sans-serif;
    font-weight: 600;
    font-size: 62px;
    line-height: 97px;
    letter-spacing: -0.5px;
    color: var(--subtitle-white);
    text-align: center;
  }
  .subtitle span { display: block; }
</style>
</head>
<body>
  <div class="book-cover">
    <div class="spine-panel">
      <h1 class="main-title">
        <span class="title-prefix">On</span>
        <span class="title-word">Momentum</span>
      </h1>
    </div>
    <div class="subtitle-panel">
      <p class="subtitle">
        <span>The</span>
        <span>Gathered</span>
        <span>Insights</span>
        <span>of the</span>
        <span>Swiftest</span>
        <span>Worker</span>
        <span>Breathing</span>
      </p>
    </div>
  </div>
</body>
</html>
```